Quill Physical Therapy Website

I would need a clean modern website built to showcase my Physical therapy brand and services. I would need a simple but descriptive website that can ultimately connect my patients to my electronic medical portal so they may book an appointment..

```html
<!DOCTYPE html>
<html lang="en">
<head>
<meta charset="utf-8">
<title>Quill Physical Therapy</title>
<link href="https://fonts.googleapis.com/css2?family=Montserrat:wght@400;500;600;700&family=Open+Sans:wght@400;600&display=swap" rel="stylesheet">
<style>
:root{
  --teal:#17726b;
  --teal-dark:#0f5f59;
  --green:#7bc043;
  --green-light:#8fd055;
  --ink:#333;
  --muted:#555;
  --light:#f1f2f2;
  --white:#fff;
}
*{box-sizing:border-box;margin:0;padding:0}
html,body{width:1200px;height:4280px;overflow:hidden;background:var(--white)}
body{position:relative;font-family:"Open Sans",Arial,sans-serif;color:var(--ink)}
.abs{position:absolute}
.head-font{font-family:"Montserrat",Arial,sans-serif}
.btn{position:absolute;display:flex;align-items:center;justify-content:center;border-radius:30px;color:var(--white);font-family:"Montserrat",Arial,sans-serif;font-weight:600;letter-spacing:.5px;text-transform:uppercase}
.btn-teal{background:var(--teal)}
.btn-green{background:var(--green)}
.photo{position:absolute}

/* header */
.topbar{left:850px;top:0;width:350px;height:52px;background:var(--teal);border-bottom-left-radius:40px;color:var(--white);font:600 14px "Montserrat",Arial,sans-serif;display:flex;align-items:center;padding-left:50px;gap:10px}
.topbar-icon{width:26px;height:26px;border:2px solid var(--white);border-radius:50%;display:flex;align-items:center;justify-content:center}
.header{left:0;top:0;width:1200px;height:142px;background:var(--white);box-shadow:0 2px 6px rgba(0,0,0,.08)}
.logo-badge{left:110px;top:0;width:218px;height:222px;border-radius:0 0 110px 110px;background:var(--white);box-shadow:0 4px 8px rgba(0,0,0,.12);display:flex;flex-direction:column;align-items:center;justify-content:center;gap:8px;padding-top:20px}
.logo-badge .mark{width:56px;height:56px;border-radius:50%;background:var(--teal)}
.logo-badge .name{font:700 36px "Montserrat",Arial,sans-serif;color:var(--teal);line-height:1}
.nav{left:494px;top:88px;display:flex;gap:52px;font:600 14px "Montserrat",Arial,sans-serif;color:#222;text-transform:uppercase}
.nav .active{color:var(--teal)}

/* hero */
.hero{left:0;top:142px;width:1200px;height:780px;background:linear-gradient(90deg,#f7f8f8 0%,#eef0ef 40%,#e4e6e4 100%)}
.hero-title{left:106px;top:410px;font:700 82px "Montserrat",Arial,sans-serif;color:var(--teal);line-height:1}
.hero-sub{left:106px;top:496px;font:600 40px "Montserrat",Arial,sans-serif;color:var(--green);line-height:1}

/* welcome */
.eyebrow{font:600 22px "Montserrat",Arial,sans-serif;color:var(--teal);text-transform:uppercase}
.welcome-title{font:600 29px "Montserrat",Arial,sans-serif;color:var(--green);text-transform:uppercase}
.body-copy{font-size:13px;line-height:27px;color:var(--muted)}

/* sections */
.section-title{width:1200px;text-align:center;font:600 34px "Montserrat",Arial,sans-serif;color:var(--teal);text-transform:uppercase}
.section-title span{color:var(--green)}
.title-rule{width:46px;height:3px;background:var(--teal);left:577px}
.service-name{font:600 19px "Montserrat",Arial,sans-serif;text-transform:uppercase}
.card-copy{font-size:12.5px;line-height:26px;color:var(--muted)}

.blog-card{position:absolute;width:288px;height:222px;background:var(--white);box-shadow:0 2px 8px rgba(0,0,0,.14);text-align:center;padding:28px 20px 0}
.blog-date{font:600 21px "Montserrat",Arial,sans-serif;color:var(--green)}
.blog-head{font:600 18px "Montserrat",Arial,sans-serif;color:#333;line-height:26px;margin-top:8px}
.blog-copy{font-size:12.5px;line-height:24px;color:var(--muted);margin-top:10px}

.ticks{list-style:none;font-size:15px;color:var(--white)}
.ticks li{display:flex;align-items:center;gap:18px;height:38.5px}

.arrow-box{width:44px;height:40px;border:2px solid var(--white);display:flex;align-items:center;justify-content:center}

.footer-head{font:500 21px "Montserrat",Arial,sans-serif;color:var(--white);text-transform:uppercase;letter-spacing:.5px}
.footer-item{display:flex;gap:22px;color:var(--white);font-size:14.5px;line-height:23px}
</style>
</head>
<body>

<!-- hero -->
<div class="abs hero"></div>
<div class="photo" role="img" aria-label="Therapist helping an older woman exercise on a therapy ball" style="left:430px;top:142px;width:770px;height:760px;background:linear-gradient(135deg,#f3f3f2 0%,#e9e4e0 45%,#d9c3b4 70%,#e98c48 100%)"></div>
<svg class="abs" style="left:0;top:760px" width="1200" height="180" viewBox="0 0 1200 180" aria-hidden="true">
  <path d="M0 60 C300 170 800 160 1200 40 L1200 180 L0 180Z" fill="var(--white)"/>
  <path d="M0 60 C300 150 800 150 1200 40 L1200 58 C820 170 320 175 0 78Z" fill="var(--green)"/>
  <path d="M0 78 C320 175 820 170 1200 58 L1200 70 C820 190 320 190 0 90Z" fill="var(--teal)"/>
</svg>
<h1 class="abs hero-title">QUILL</h1>
<div class="abs hero-sub">PHYSICAL THERAPY</div>
<div class="btn btn-teal" style="left:106px;top:566px;width:160px;height:56px;font-size:15px">Read More</div>

<!-- header -->
<div class="abs header"></div>
<div class="abs topbar"><span class="topbar-icon"><svg width="12" height="12" viewBox="0 0 12 12"><rect x="1" y="2" width="10" height="9" fill="none" stroke="#fff" stroke-width="1.5"/><line x1="1" y1="5" x2="11" y2="5" stroke="#fff" stroke-width="1.5"/></svg></span>BOOK AN APPOINTMENT</div>
<div class="abs logo-badge"><span class="mark"></span><span class="name">QUILL</span></div>
<nav class="abs nav"><span class="active">Home</span><span>About Us</span><span>Services</span><span>News</span><span>Contact Us <span style="color:var(--green)">| &#9906;</span></span></nav>

<!-- welcome -->
<div class="abs eyebrow" style="left:112px;top:1000px">Welcome to</div>
<h2 class="abs welcome-title" style="left:112px;top:1034px">Quill Physical Therapy</h2>
<p class="abs body-copy" style="left:112px;top:1094px;width:478px">Sed ut perspiciatis unde omnis iste natus error sit voluptatem accusantium dol oremque laudantium, totam rem aperiam, eaque ipsa quae ab illo inventore veritatis et quasi architecto beatae vitae dicta sunt explicabo. Nemo enim ipsam volupt atem quia voluptas sit aspernatur aut odit aut fugit, sed quia consequunt ur magni dolores eos qui ratione voluptatem sequi nesciunt.Neque porro quisq uam est, qui dolorem ipsum quia dolor sit amet, consectetur, adipisci velit, sed quia non numquam eius modi tempora incidunt ut labore et dolore magnam aliequ modi tempora quam quaerat voluptatem. Ut enim ad minima veniam, quis nostrum exercitationem ullam corporis suscipit laboriosam, nisi ut aliquid ullam corporis suscipit &nbsp;exea commodi consequatur</p>
<div class="btn btn-teal" style="left:112px;top:1394px;width:160px;height:56px;font-size:15px">Read More</div>
<div class="abs" style="left:700px;top:1140px;display:flex;align-items:center;gap:22px">
  <span style="width:90px;height:90px;border-radius:50%;background:var(--teal)"></span>
  <span class="head-font" style="font-size:84px;font-weight:700;color:var(--teal);line-height:1">QUILL</span>
</div>

<!-- services -->
<div class="abs" style="left:0;top:1525px;width:1200px;height:632px;background:linear-gradient(90deg,#f4f4f4,#ececec 50%,#f4f4f4)"></div>
<h2 class="abs section-title" style="left:0;top:1578px">Our <span>Services</span></h2>
<div class="abs title-rule" style="top:1627px"></div>

<div class="photo" role="img" aria-label="Therapist stretching a patient's leg" style="left:112px;top:1678px;width:236px;height:196px;background:linear-gradient(135deg,#4f86c4,#bcc6cc)"></div>
<div class="photo" role="img" aria-label="Therapist treating a patient on a table" style="left:358px;top:1678px;width:236px;height:196px;background:linear-gradient(135deg,#c9ced0,#7d7f80)"></div>
<div class="photo" role="img" aria-label="Therapist guiding a woman through a floor exercise" style="left:605px;top:1678px;width:236px;height:196px;background:linear-gradient(135deg,#5c5f63,#b9bcbe)"></div>
<div class="photo" role="img" aria-label="Older woman lifting a small dumbbell" style="left:852px;top:1678px;width:236px;height:196px;background:linear-gradient(135deg,#d9d3c9,#8d9fb8)"></div>

<div class="abs service-name" style="left:112px;top:1896px;color:var(--teal)">Services 01</div>
<div class="abs service-name" style="left:358px;top:1896px;color:var(--green)">Services 02</div>
<div class="abs service-name" style="left:605px;top:1896px;color:var(--teal)">Services 03</div>
<div class="abs service-name" style="left:852px;top:1896px;color:var(--green)">Services 04</div>
<p class="abs card-copy" style="left:112px;top:1934px;width:236px">Sed ut perspiciatis unde omnis iste na tus error sit voluptatem accusant ium doloremque laudantium</p>
<p class="abs card-copy" style="left:358px;top:1934px;width:236px">Sed ut perspiciatis unde omnis iste na tus error sit voluptatem accusant ium doloremque laudantium</p>
<p class="abs card-copy" style="left:605px;top:1934px;width:236px">Sed ut perspiciatis unde omnis iste na tus error sit voluptatem accusant ium doloremque laudantium</p>
<p class="abs card-copy" style="left:852px;top:1934px;width:236px">Sed ut perspiciatis unde omnis iste na tus error sit voluptatem accusant ium doloremque laudantium</p>
<div class="btn btn-teal" style="left:112px;top:2028px;width:116px;height:40px;font-size:11.5px">Read More</div>
<div class="btn btn-green" style="left:358px;top:2028px;width:116px;height:40px;font-size:11.5px">Read More</div>
<div class="btn btn-teal" style="left:605px;top:2028px;width:116px;height:40px;font-size:11.5px">Read More</div>
<div class="btn btn-green" style="left:852px;top:2028px;width:116px;height:40px;font-size:11.5px">Read More</div>

<!-- what we do -->
<div class="abs" style="left:0;top:2158px;width:1200px;height:577px;background:linear-gradient(90deg,var(--green) 0%,var(--green-light) 45%,#e8ece8 62%,#f2f2f2 100%)"></div>
<div class="photo" role="img" aria-label="Therapist supporting an older man's shoulder and arm" style="left:525px;top:2158px;width:675px;height:577px;background:linear-gradient(90deg,rgba(143,208,85,0) 0%,#c9b8a8 35%,#d23a3a 55%,#e6e6e6 100%)"></div>
<h2 class="abs head-font" style="left:112px;top:2215px;font-size:34px;font-weight:600;color:var(--white)">WHAT WE DO</h2>
<div class="abs" style="left:112px;top:2268px;width:52px;height:3px;background:var(--white)"></div>
<p class="abs" style="left:112px;top:2298px;width:410px;font-size:12.5px;line-height:26px;color:var(--white)">Sed ut perspiciatis unde omnis iste natus error sit voluptatem accus antium doloremque laudantium, totam rem aperiam, eaque ipsa quasi architecto beatae vitae dicta sunt explicabo.</p>
<ul class="abs ticks" style="left:112px;top:2394px">
  <li><svg width="14" height="12" viewBox="0 0 14 12"><path d="M1 6l4 4 8-9" fill="none" stroke="#fff" stroke-width="2.5"/></svg>Sed ut perspiciatis unde omnis iste natus enim ipsam</li>
  <li><svg width="14" height="12" viewBox="0 0 14 12"><path d="M1 6l4 4 8-9" fill="none" stroke="#fff" stroke-width="2.5"/></svg>Error sit voluptatem accus antium luptatem</li>
  <li><svg width="14" height="12" viewBox="0 0 14 12"><path d="M1 6l4 4 8-9" fill="none" stroke="#fff" stroke-width="2.5"/></svg>Doloremque laudantium, totam rem unde</li>
  <li><svg width="14" height="12" viewBox="0 0 14 12"><path d="M1 6l4 4 8-9" fill="none" stroke="#fff" stroke-width="2.5"/></svg>Aperiam, eaque ipsa &nbsp;quasi architecto omnis</li>
  <li><svg width="14" height="12" viewBox="0 0 14 12"><path d="M1 6l4 4 8-9" fill="none" stroke="#fff" stroke-width="2.5"/></svg>Beatae vitae dicta sunt explicabo</li>
</ul>
<div class="btn btn-teal" style="left:112px;top:2610px;width:152px;height:54px;font-size:14px">Read More</div>

<!-- blog -->
<h2 class="abs section-title" style="left:0;top:2782px">Latest <span>Blog</span></h2>
<div class="abs title-rule" style="top:2831px"></div>
<div class="photo" role="img" aria-label="Woman exercising with a blue therapy ball beside a therapist" style="left:112px;top:2867px;width:312px;height:278px;background:linear-gradient(135deg,#e4e4e4,#3e7fc4 60%,#d0d0d0)"></div>
<div class="photo" role="img" aria-label="Patient stretching over a ball with therapist assistance" style="left:444px;top:2867px;width:312px;height:278px;background:linear-gradient(135deg,#d9e6ee,#8a9198 60%,#cfd6da)"></div>
<div class="photo" role="img" aria-label="Group of older women exercising with small weights" style="left:776px;top:2867px;width:312px;height:278px;background:linear-gradient(135deg,#c7cdd0,#d89090 55%,#e7e2dc)"></div>
<div class="blog-card" style="left:128px;top:3085px"><div class="blog-date">08 SEP 2021</div><div class="blog-head">Sed ut perspiciatis unde omnis iste natus</div><p class="blog-copy">Nemo enim ipsam voluptatem quia voluptas sit aspernatur aut odit aut fugit, eos qui ratione voluptatem</p></div>
<div class="blog-card" style="left:460px;top:3085px"><div class="blog-date">08 SEP 2021</div><div class="blog-head">Sed ut perspiciatis unde omnis iste natus</div><p class="blog-copy">Nemo enim ipsam voluptatem quia voluptas sit aspernatur aut odit aut fugit, eos qui ratione voluptatem</p></div>
<div class="blog-card" style="left:792px;top:3085px"><div class="blog-date">08 SEP 2021</div><div class="blog-head">Sed ut perspiciatis unde omnis iste natus</div><p class="blog-copy">Nemo enim ipsam voluptatem quia voluptas sit aspernatur aut odit aut fugit, eos qui ratione voluptatem</p></div>

<!-- testimonial + footer -->
<div class="abs" style="left:0;top:3372px;width:1200px;height:908px;background:linear-gradient(180deg,var(--green) 0%,var(--green-light) 40%,var(--green) 100%)"></div>
<svg class="abs" style="left:0;top:3760px" width="1200" height="520" viewBox="0 0 1200 520" aria-hidden="true">
  <path d="M0 40 C400 110 800 100 1200 30 L1200 520 L0 520Z" fill="var(--teal)"/>
</svg>
<div class="photo" role="img" aria-label="Portrait of a smiling older woman" style="left:540px;top:3380px;width:120px;height:120px;border-radius:50%;border:4px solid var(--white);background:linear-gradient(135deg,#e8e2dc,#c8a89a)"></div>
<div class="abs arrow-box" style="left:165px;top:3568px"><svg width="10" height="14" viewBox="0 0 10 14"><path d="M8 1L2 7l6 6" fill="none" stroke="#fff" stroke-width="2"/></svg></div>
<div class="abs arrow-box" style="left:978px;top:3568px"><svg width="10" height="14" viewBox="0 0 10 14"><path d="M2 1l6 6-6 6" fill="none" stroke="#fff" stroke-width="2"/></svg></div>
<p class="abs" style="left:230px;top:3558px;width:740px;text-align:center;font-size:14.5px;line-height:26px;font-style:italic;color:var(--white)"><span style="font:700 34px Georgia,serif;vertical-align:-8px">&ldquo;</span>Sed ut perspiciatis unde omnis iste natus error sit voluptatem accusantium doloremque laudantium, totam rem aperiam, eaque ipsa quae ab illo inventore veritatis et quasi architecto beatae vitae dicta sunt explicabo. Nemo enim ipsam voluptatem quia voluptas sit aspernatur aut odit aut fugit, sed quia consequuntur magni dolores eos qui ratione voluptatem sequi nesciunt.<span style="font:700 34px Georgia,serif;vertical-align:-16px">&rdquo;</span></p>
<div class="abs head-font" style="left:0;top:3697px;width:1200px;text-align:center;font-size:18px;font-weight:600;color:var(--white)">-DANA REYES</div>

<div class="abs" style="left:140px;top:3960px;display:flex;flex-direction:column;align-items:center;gap:16px">
  <span style="width:110px;height:110px;border-radius:50%;background:var(--white)"></span>
  <span class="head-font" style="font-size:60px;font-weight:700;color:var(--white);line-height:1">QUILL</span>
</div>

<div class="abs footer-head" style="left:472px;top:3918px">Contact Us</div>
<div class="abs" style="left:472px;top:3964px;display:flex;flex-direction:column;gap:26px">
  <div class="footer-item"><svg width="18" height="22" viewBox="0 0 18 22"><path d="M9 21s7-7 7-12A7 7 0 0 0 2 9c0 5 7 12 7 12z" fill="none" stroke="#fff" stroke-width="1.5"/><circle cx="9" cy="9" r="2.5" fill="none" stroke="#fff" stroke-width="1.5"/></svg><div>Address<br>250 ipsam voluptatem<br>quia voluptas</div></div>
  <div class="footer-item"><svg width="18" height="20" viewBox="0 0 18 20"><path d="M4 1l3 4-2 2c1 3 3 5 6 7l2-2 4 3-2 3C8 18 1 10 1 4z" fill="none" stroke="#fff" stroke-width="1.5"/></svg><div>Phone :<br>000-121-1231</div></div>
  <div class="footer-item"><svg width="20" height="14" viewBox="0 0 20 14"><rect x="1" y="1" width="18" height="12" fill="none" stroke="#fff" stroke-width="1.5"/><path d="M1 1l9 7 9-7" fill="none" stroke="#fff" stroke-width="1.5"/></svg><div>Email :<br>info@company.com</div></div>
</div>

<div class="abs footer-head" style="left:748px;top:3915px">Newsletter</div>
<p class="abs" style="left:748px;top:3962px;width:330px;font-size:13px;line-height:24px;color:var(--white)">Sed ut perspiciatis unde omnis iste natus error sit voluptatem accusantium doloremque</p>
<div class="abs" style="left:748px;top:4032px;width:324px;height:42px;background:var(--white);border:1px solid #ccc;font-size:13px;color:#444;display:flex;align-items:center;padding-left:18px">Enter Email</div>
<div class="abs" style="left:748px;top:4094px;width:136px;height:42px;background:var(--green);color:var(--white);font:600 14px 'Montserrat',Arial,sans-serif;display:flex;align-items:center;justify-content:center">SUBSCRIBE</div>

<div class="abs" style="left:0;top:4228px;width:1200px;text-align:center;font-size:14.5px;color:var(--white)">&copy; Copyright 2021.All Rights Reserved</div>

</body>
</html>
```